Flyer for the Radiant Harvest Worship Day

I am looking to create a flyer for a one day prayer retreat our church is organizing.
This flyer will be posted on social media, websites and will also be printed so it can be mailed to people.
I am looking for something professional, with good use of our logo and band colors (logo colors).
I am counting on the designer's skill, creativity, art and knowledge of media communication to produce a flyer that will effectively and quickly convey the message we are trying to spread.
CONTENT OF THE FLYER:
Event title: Radiant Harvest Worship Day
Date: Tuesday July 2nd, 2019
Time: 11:00AM - 7:00PM
Belmora Hotel, 4875 Wexley Avenue, Portland, Maine 04102 (Room: Juniper)
Event Key words to highlight what the event is about: Prayer, Sharing the Word, Panel discussion, prophecy, Impartation.
Key phrases:
A one day prayer retreat.
Jesus Chris is Lord
Contact info:
www.tolvex.org
Phone: 207 555 3184
Email: contact@brookhavenfold.org

```html
<!DOCTYPE html>
<html lang="en">
<head>
<meta charset="utf-8">
<title>Radiant Harvest Worship Day</title>
<link href="https://fonts.googleapis.com/css2?family=Oswald:wght@500;600&family=Arimo:wght@400;700&display=swap" rel="stylesheet">
<style>
  :root{
    --navy:#0d3a5e;
    --navy-deep:#0a3355;
    --orange:#f39220;
    --photo-dark:#2f2433;
    --photo-mid:#4a3846;
    --photo-light:#6b5560;
    --white:#ffffff;
    --frame:#c9c9c9;
  }
  *{margin:0;padding:0;box-sizing:border-box}
  html,body{width:881px;height:1200px;overflow:hidden;background:var(--white)}
  .canvas{position:relative;width:881px;height:1200px;border:1px solid var(--frame);background:var(--white)}
  .flyer{position:absolute;left:40px;top:34px;width:792px;height:1119px;background:var(--navy);overflow:hidden}
  .hero-photo{position:absolute;left:0;top:34px;width:792px;height:549px;
    background:radial-gradient(ellipse 45% 60% at 72% 55%, var(--photo-light) 0%, var(--photo-mid) 45%, var(--photo-dark) 100%)}
  .brand-box{position:absolute;left:66px;top:34px;width:207px;height:172px;background:var(--navy);
    display:flex;align-items:center;justify-content:center;gap:10px}
  .brand-mark{width:14px;height:14px;border-radius:50%;background:var(--orange)}
  .brand-name{font-family:"Oswald",sans-serif;font-weight:500;font-size:38px;letter-spacing:2px;color:var(--white)}
  .event-title{position:absolute;left:47px;top:300px;font-family:"Oswald",sans-serif;font-weight:600;text-transform:uppercase;line-height:1}
  .event-title .line-top{display:block;font-size:50px;color:var(--white);letter-spacing:-.5px}
  .event-title .line-bottom{display:block;font-size:72px;color:var(--orange);letter-spacing:-1px;margin-top:2px}
  .tagline-band{position:absolute;left:0;top:595px;width:792px;height:96px;background:var(--orange);
    text-align:center;color:var(--white);font-family:"Arimo",sans-serif}
  .tagline-band .retreat{display:block;font-size:29px;font-weight:400;padding-top:10px;letter-spacing:.3px}
  .tagline-band .declaration{display:block;font-size:45px;font-weight:700;line-height:1.05}
  .keywords{position:absolute;left:0;top:725px;width:792px;text-align:center;color:var(--white);
    font-family:"Arimo",sans-serif;font-weight:700;font-size:28px;line-height:41px}
  .info-row{position:absolute;display:flex;align-items:center;color:var(--white);font-family:"Arimo",sans-serif;font-size:22px}
  .info-row .icon{width:36px;height:36px;border-radius:50%;background:var(--orange);display:flex;align-items:center;justify-content:center;margin-right:12px;flex:none}
  .info-date{left:108px;top:849px}
  .info-time{left:432px;top:849px}
  .info-place{left:45px;top:901px}
  .divider{position:absolute;left:32px;top:1001px;width:726px;height:1px;background:rgba(255,255,255,.55)}
  .footer-brand{position:absolute;left:68px;top:1030px;display:flex;align-items:center;gap:9px}
  .footer-brand .brand-name{font-size:42px}
  .contact{position:absolute;left:276px;top:1016px;color:var(--white);font-family:"Arimo",sans-serif;font-size:30px;line-height:40px}
  .contact-line{display:flex;align-items:center;gap:10px}
  .contact-line svg{flex:none}
</style>
</head>
<body>
<div class="canvas">
  <div class="flyer">
    <div class="hero-photo" role="img" aria-label="Photograph of a young child with eyes closed, hands folded in prayer"></div>

    <div class="brand-box">
      <span class="brand-mark"></span>
      <span class="brand-name">TOLVEX</span>
    </div>

    <h1 class="event-title">
      <span class="line-top">Radiant Harvest</span>
      <span class="line-bottom">Worship Day</span>
    </h1>

    <div class="tagline-band">
      <span class="retreat">A ONE DAY PRAYER RETREAT.</span>
      <span class="declaration">JESUS CHRIS IS LORD</span>
    </div>

    <p class="keywords">Prayer | Sharing the Word<br>Panel discussion | Prophecy | Impartation.</p>

    <div class="info-row info-date">
      <span class="icon"><svg width="20" height="20" viewBox="0 0 20 20" fill="none" stroke="#fff" stroke-width="1.6"><rect x="2.5" y="4" width="15" height="13.5" rx="1.5"/><line x1="2.5" y1="8" x2="17.5" y2="8"/><line x1="6.5" y1="2" x2="6.5" y2="5.5"/><line x1="13.5" y1="2" x2="13.5" y2="5.5"/></svg></span>
      Tuesday July 2nd, 2019
    </div>
    <div class="info-row info-time">
      <span class="icon"><svg width="20" height="20" viewBox="0 0 20 20" fill="none" stroke="#fff" stroke-width="1.6"><circle cx="10" cy="10" r="7.5"/><polyline points="10,5.5 10,10 13,12"/></svg></span>
      11:00AM - 7:00PM
    </div>
    <div class="info-row info-place">
      <span class="icon"><svg width="20" height="20" viewBox="0 0 20 20" fill="none" stroke="#fff" stroke-width="1.6"><path d="M10 18s-5.5-6-5.5-10a5.5 5.5 0 0 1 11 0c0 4-5.5 10-5.5 10z"/><circle cx="10" cy="8" r="2"/></svg></span>
      Belmora Hotel, 4875 Wexley Avenue, Portland, Maine 04102
    </div>

    <div class="divider"></div>

    <div class="footer-brand">
      <span class="brand-mark"></span>
      <span class="brand-name">TOLVEX</span>
    </div>

    <div class="contact">
      <div class="contact-line">
        <svg width="24" height="24" viewBox="0 0 24 24" fill="none" stroke="#fff" stroke-width="1.4"><circle cx="12" cy="12" r="9.5"/><ellipse cx="12" cy="12" rx="4.2" ry="9.5"/><line x1="2.5" y1="12" x2="21.5" y2="12"/><path d="M4 7h16M4 17h16"/></svg>
        tolvex.org
        <svg width="28" height="24" viewBox="0 0 28 24" fill="none" stroke="#fff" stroke-width="1.4" style="margin-left:6px"><path d="M3 9c0-3 5-5 11-5s11 2 11 5v2h-5V8.5c-2-1-10-1-12 0V11H3z"/><path d="M8 11l-2 9h16l-2-9"/><circle cx="14" cy="15" r="2.5"/></svg>
        207 555 3184
      </div>
      <div class="contact-line">
        <svg width="24" height="20" viewBox="0 0 24 20" fill="none" stroke="#fff" stroke-width="1.4"><rect x="1.5" y="2.5" width="21" height="15"/><polyline points="1.5,2.5 12,11 22.5,2.5"/></svg>
        contact@brookhavenfold.org
      </div>
    </div>
  </div>
</div>
</body>
</html>
```